The Lark Whiskey & Coffee - Bar Menu

The Lark is a speakeasy style coffee and whiskey bar. Upscale with design elements tying in both prohibition era elegance and modern touches.

Black and Gold are our colors. (see logo)

We would need a 8 page menu- front and back. 4.24 in x 11 in for each page. The pages would be:

Intro page
Food/Dessert
Cocktails x 2 pages
Wine- Glass Pour
Wine- Bottle only
Beer
Non-Alcoholic Beverages

Attached is the menu cocktails and food/non alcoholic.

We need an editable format as this menu would be constantly changing.

UPDATE: The owner would potentially like to see the use of the original floor plans incorporated into the menu design. I have uploaded those to this brief.

UPDATE: I have added some photos that show the style the owner would like the writing to be displayed.

Requirements
Should not have
• No pictures of wine or beer or other images. Clipart could be fine, but we want to showcase class and an upscale vibe.

```html
<!DOCTYPE html>
<html lang="en">
<head>
<meta charset="utf-8">
<title>The Lark Whiskey &amp; Coffee – Bar Menu</title>
<link rel="stylesheet" href="https://fonts.googleapis.com/css2?family=Cinzel:wght@600;700&family=Montserrat:ital,wght@0,400;0,500;0,700;1,400&family=Yellowtail&display=swap">
<style>
  :root {
    --stage: #d8b142;
    --panel: #0e0e0e;
    --gold: #d6ad45;
    --ink: #f2efe8;
    --muted: #c9c6bf;
    --frame: #6e7177;
    --banner: #3b392b;
  }
  * { box-sizing: border-box; margin: 0; padding: 0; }
  html, body { width: 1200px; height: 1200px; overflow: hidden; }
  body { background: var(--stage); font-family: "Montserrat", sans-serif; color: var(--ink); position: relative; }

  .page { position: absolute; width: 261px; height: 673px; background: var(--panel); overflow: hidden; }
  .page--intro { left: 34px; top: 120px; }
  .page--food { left: 324px; top: 407px; }
  .page--cocktails-a { left: 615px; top: 120px; }
  .page--cocktails-b { left: 906px; top: 407px; }

  .frame { position: absolute; left: 16px; right: 16px; top: 16px; bottom: 17px; border: 1px solid var(--frame); pointer-events: none; }
  .frame::before, .frame::after { content: ""; position: absolute; width: 6px; height: 6px; border: 1px solid var(--frame); }
  .frame::before { left: -5px; top: -5px; }
  .frame::after { right: -5px; bottom: -5px; }
  .page--intro .frame { top: 49px; bottom: 17px; }
  .frame-gap { position: absolute; top: 47px; left: 100px; width: 61px; height: 4px; background: var(--panel); }

  .photo { position: absolute; left: 0; right: 0; bottom: 0; }

  .page-title { position: absolute; left: 0; right: 0; text-align: center; font-family: "Cinzel", serif; font-weight: 700; color: var(--gold); font-size: 23px; letter-spacing: 1px; }
  .divider { position: absolute; left: 50%; transform: translateX(-50%); width: 98px; height: 8px; }

  .brand { position: absolute; left: 0; right: 0; top: 92px; text-align: center; color: var(--gold); font-weight: 700; font-size: 17px; letter-spacing: 2px; line-height: 1.1; }
  .brand small { display: block; font-size: 9px; letter-spacing: 1.2px; margin-top: 2px; font-weight: 700; }
  .brand-mark { position: absolute; left: 120px; top: 30px; width: 22px; height: 22px; background: var(--gold); }
  .notice { position: absolute; left: 30px; right: 30px; top: 140px; text-align: center; font-size: 9.6px; line-height: 1.3; }

  .promo { position: absolute; left: 48px; top: 214px; width: 165px; height: 284px; }
  .promo svg { position: absolute; inset: 0; }
  .promo-body { position: absolute; inset: 0; text-align: center; }
  .promo-script { position: absolute; left: 0; right: 0; top: 10px; font-family: "Yellowtail", cursive; color: var(--gold); font-size: 22px; }
  .promo-terms { position: absolute; left: 0; right: 0; top: 43px; font-weight: 700; font-size: 14.5px; line-height: 1.18; letter-spacing: .3px; }
  .promo-note { position: absolute; left: 0; right: 0; top: 112px; font-size: 9.6px; line-height: 1.3; }
  .promo-rule { position: absolute; left: 34px; top: 158px; width: 97px; height: 6px; }
  .promo-rate { position: absolute; left: 0; right: 0; top: 172px; font-family: "Cinzel", serif; font-weight: 700; color: var(--gold); font-size: 23px; }
  .promo-fee { position: absolute; left: 0; right: 0; top: 204px; font-size: 9.6px; line-height: 1.3; }

  .menu-list { position: absolute; left: 33px; right: 32px; }
  .item { margin-bottom: 10px; }
  .item-name { font-size: 10.8px; font-weight: 500; letter-spacing: .6px; line-height: 1.25; }
  .item-desc { font-size: 7.6px; font-style: italic; color: var(--muted); line-height: 1.35; }
  .priced { display: flex; align-items: baseline; }
  .priced .dots { flex: 1; border-bottom: 1px dotted var(--ink); margin: 0 2px; transform: translateY(-3px); }

  .section { position: absolute; left: 33px; right: 32px; }
  .section-head { display: flex; align-items: flex-end; gap: 4px; margin-bottom: 3px; }
  .section-label { font-family: "Cinzel", serif; font-weight: 700; color: var(--gold); font-size: 14.5px; letter-spacing: .6px; line-height: 1; }
  .section-line { flex: 1; border-bottom: 1px solid var(--frame); margin-bottom: 2px; }
  .section-icon { width: 18px; height: 24px; border-radius: 3px; background: rgba(214,173,69,.18); flex: none; }
  .section .item { margin-bottom: 9px; }
</style>
</head>
<body>

<section class="page page--intro">
  <div class="frame"></div>
  <div class="frame-gap"></div>
  <div class="brand-mark"></div>
  <div class="brand">THE LARK<small>WHISKEY &amp; COFFEE</small></div>
  <p class="notice">The Lark Whiskey &amp; Coffee Reserves the right to change menus selections, and/or the prices that accompany those items, as they appear on the menus at the restaurant.</p>

  <div class="promo">
    <svg viewBox="0 0 165 284" preserveAspectRatio="none">
      <polygon points="0,0 165,0 165,32 155,40 155,238 82.5,284 10,238 10,40 0,32" fill="var(--banner)"/>
    </svg>
    <div class="promo-body">
      <div class="promo-script">Only one</div>
      <div class="promo-terms">PROMOTION<br>SPECIAL<br>DISCOUNT<br>KICKBACK</div>
      <div class="promo-note">MAY BE USED<br>AT ONE TIME,<br>PER TABLE OR CHECK</div>
      <svg class="promo-rule" viewBox="0 0 97 6"><line x1="0" y1="3" x2="97" y2="3" stroke="var(--ink)" stroke-width=".6"/><rect x="45.5" y="0.5" width="5" height="5" transform="rotate(45 48 3)" fill="var(--ink)"/></svg>
      <div class="promo-rate">20%</div>
      <div class="promo-fee">SERVICE CHARGED<br>ADDED ONTO BILLS OF<br>PARTIES OF 6 OR MORE</div>
    </div>
  </div>

  <div class="photo" role="img" aria-label="Photo of a crystal whiskey tumbler with ice on a wooden bar top" style="top:507px;background:radial-gradient(ellipse at 50% 60%, #8a4a1a 0%, #4a2410 35%, #1a0e08 70%, #0e0e0e 100%);"></div>
</section>

<section class="page page--food">
  <div class="frame"></div>
  <h2 class="page-title" style="top:31px">FOOD</h2>
  <svg class="divider" style="top:62px" viewBox="0 0 98 8"><line x1="0" y1="4" x2="98" y2="4" stroke="var(--gold)" stroke-width=".7"/><rect x="46" y="1" width="6" height="6" transform="rotate(45 49 4)" fill="var(--gold)"/></svg>

  <div class="menu-list" style="top:77px">
    <div class="item"><div class="item-name priced"><span>Bone Marrow</span><span class="dots"></span><span>$20</span></div><div class="item-desc">Bone marrow roasted with sea salt and served with warm tortillas</div></div>
    <div class="item"><div class="item-name priced"><span>Charcuterie Board</span><span class="dots"></span><span>$25</span></div><div class="item-desc">Assorted artisan meats and cheeses, nuts, &amp; fruits</div></div>
    <div class="item"><div class="item-name priced"><span>Hummus, Veggie, &amp; Pita</span><span class="dots"></span><span>$16</span></div><div class="item-desc">Assorted vegetables with warm pita and roasted garlic hummus</div></div>
    <div class="item"><div class="item-name priced"><span>Lamb Chops</span><span class="dots"></span><span>$18</span></div><div class="item-desc">Lamb chops broiled with rosemary</div></div>
    <div class="item"><div class="item-name priced"><span>Tuna Tower</span><span class="dots"></span><span>$17</span></div><div class="item-desc">Fresh tuna served with white rice, avocado &amp; spice</div></div>
    <div class="item"><div class="item-name priced"><span>Lettuce Wrap-Walnut Shrimp</span><span class="dots"></span><span>$13</span></div><div class="item-desc">Honey walnut aioli coated shrimp and lettuce cups with a candied walnut</div></div>
  </div>

  <h2 class="page-title" style="top:335px">DESSERTS</h2>
  <svg class="divider" style="top:366px" viewBox="0 0 98 8"><line x1="0" y1="4" x2="98" y2="4" stroke="var(--gold)" stroke-width=".7"/><rect x="46" y="1" width="6" height="6" transform="rotate(45 49 4)" fill="var(--gold)"/></svg>
  <div class="menu-list" style="top:386px">
    <div class="item" style="margin-bottom:14px"><div class="item-name">Tart</div><div class="item-desc">Your choice of apple or berry with vanilla ice cream</div></div>
    <div class="item"><div class="item-name">Cheesecake</div><div class="item-desc">Chocolate or strawberry drizzle</div></div>
  </div>

  <div class="photo" role="img" aria-label="Photo of a brownie topped with vanilla ice cream, chocolate drizzle and mint" style="top:463px;background:radial-gradient(ellipse at 50% 50%, #6b5a45 0%, #2d241c 40%, #0e0e0e 75%);"></div>
</section>

<section class="page page--cocktails-a">
  <div class="frame"></div>
  <h2 class="page-title" style="top:33px">COCKTAILS</h2>
  <svg class="divider" style="top:64px" viewBox="0 0 98 8"><line x1="0" y1="4" x2="98" y2="4" stroke="var(--gold)" stroke-width=".7"/><rect x="46" y="1" width="6" height="6" transform="rotate(45 49 4)" fill="var(--gold)"/></svg>

  <div class="section" style="top:76px">
    <div class="section-head"><span class="section-label">VODKA</span><span class="section-line"></span><span class="section-icon" role="img" aria-label="Line icon of a cocktail glass"></span></div>
    <div class="item"><div class="item-name">The Affair</div><div class="item-desc">Vodka (strawberry/orange infusion), Lemon Oleo Saccahrum, PeaFlower Gin Float (Blue) (N&amp;N)</div></div>
    <div class="item"><div class="item-name">Bootleggers Gold</div><div class="item-desc">Vodka, Yellow Cloister, Pineapple, Lime Juice, Simple Syrup, Lemon Zest</div></div>
  </div>

  <div class="section" style="top:187px">
    <div class="section-head"><span class="section-label">TEQUILA</span><span class="section-line"></span><span class="section-icon" role="img" aria-label="Line icon of a garnished cocktail glass"></span></div>
    <div class="item"><div class="item-name">The Mayan</div><div class="item-desc">Casa Alta Blanco, Raicilla (non-peaty Mezcal), Green Cloister, Pistachio Liqueur, Olive, Lime</div></div>
    <div class="item"><div class="item-name">Toreador*</div><div class="item-desc">Blanco, Mezcal, Apricot Cordial, Lime Juice, Grape Fruit oil (oleo), Mezcal Mist</div></div>
  </div>

  <div class="section" style="top:296px">
    <div class="section-head"><span class="section-label">RUM</span><span class="section-line"></span><span class="section-icon" role="img" aria-label="Line icon of a rocks glass with ice"></span></div>
    <div class="item"><div class="item-name">Smugglers Cove**</div><div class="item-desc">Rum (Cuban), Pomegranite Liqueur, Lemon Juice, Macadamia Orgeat, Cocoa Bitters (Eggwhite)</div></div>
    <div class="item"><div class="item-name">Mary Pickwell*</div><div class="item-desc">Rum (Blanco Cuban), Pineapple, Maraschino Liqueur, Grenadine</div></div>
    <div class="item"><div class="item-name">Roy Rum Runner (Local)</div><div class="item-desc">Rum (Blanco), Rhum Agricole (non-peat Mezcal) Lime Juice, Simple Syrup w/in season fruit</div></div>
  </div>

  <div class="section" style="top:450px">
    <div class="section-head"><span class="section-label">GIN</span><span class="section-line"></span><span class="section-icon" role="img" aria-label="Line icon of a tall cocktail glass with straw"></span></div>
    <div class="item"><div class="item-name">Clover Club*</div><div class="item-desc">Azure Gin, Rasperry Liquor, Lemon Juice, Raspberries, Vanilla, Prosecco, Milk (Clarified)</div></div>
    <div class="item"><div class="item-name">Clover Club#2**</div><div class="item-desc">Gin, Marlow Vermouth, Raspberry, Lemon Juice, EggWhite</div></div>
    <div class="item"><div class="item-name">Limonata</div><div class="item-desc">Gin (Lemon infused), Limoncello, Lemon Curd, Lemon Juice, Fontella Limonata</div></div>
    <div class="item"><div class="item-name">Colony Cocktail</div><div class="item-desc">Gin, Pink Grapefruit, Maraschino Liqueur, Grapefruit twist</div></div>
  </div>
</section>

<section class="page page--cocktails-b">
  <div class="frame"></div>
  <h2 class="page-title" style="top:31px">COCKTAILS</h2>
  <svg class="divider" style="top:62px" viewBox="0 0 98 8"><line x1="0" y1="4" x2="98" y2="4" stroke="var(--gold)" stroke-width=".7"/><rect x="46" y="1" width="6" height="6" transform="rotate(45 49 4)" fill="var(--gold)"/></svg>

  <div class="section" style="top:81px">
    <div class="section-head"><span class="section-label">WHISKEY</span><span class="section-line"></span></div>
    <div class="item" style="margin-bottom:13px"><div class="item-name">The Dark Walnut</div><div class="item-desc">Irish Whiskey, Walnut Liqueur,<br>Agave Nectar, Expresso</div></div>
    <div class="item" style="margin-bottom:13px"><div class="item-name">Penicillin*</div><div class="item-desc">Blackhill Blend, Kelport Islay, Lemon Juice, Ginger, Honey Syrup (R)(Candied Ginger Garnish)</div></div>
    <div class="item" style="margin-bottom:13px"><div class="item-name">Alfred Hubbell (Local Bootlegger)</div><div class="item-desc">Elm Ridge, Honey Liqueur,<br>Lemon Juice, Habanero Bitters</div></div>
    <div class="item" style="margin-bottom:13px"><div class="item-name">Rockwell** (NY Sour)</div><div class="item-desc">Bourbon, Demerara Simple Syrup,<br>Lemon Juice, Redwine Float</div></div>
    <div class="item" style="margin-bottom:13px"><div class="item-name">Decadence</div><div class="item-desc">Blended Scotch/Whiskey, Sweet Sherry,<br>Dry Sherry, Chocolate Bitters, Orange,<br>Raspberry</div></div>
    <div class="item"><div class="item-name">Gold Rush**</div><div class="item-desc">Bourbon, Honey Syrup, Amaro,<br>Lemon Juice (Eggwhite)</div></div>
  </div>

  <div class="section" style="top:405px">
    <div class="section-head"><span class="section-label">CORDIALS</span><span class="section-line"></span></div>
    <div class="item" style="margin-bottom:13px"><div class="item-name">The Wax Poet</div><div class="item-desc">Cognac, Beeswax, Toasted Almond Liqueur,<br>Marigold Liqueur, Lime</div></div>
    <div class="item"><div class="item-name">The Bohemian</div><div class="item-desc">Cognac, Brown Butter, Dark Rum,<br>Orange Liqueur, Pear Liqueur, Bitters</div></div>
  </div>

  <div class="photo" role="img" aria-label="Photo of a cut-crystal glass with a pink cocktail and a rosemary sprig" style="top:518px;background:radial-gradient(ellipse at 50% 60%, #5a2c3a 0%, #2a1a22 40%, #0e0e0e 78%);"></div>
</section>

</body>
</html>
```